BLS Business Card 2018

Larkmere Chiropractic. We have two locations that we want to advertise on the same card. Brightvale OrthoCore campus address: 3815 Pellham Dr., Suite 240, Flowood, MS 39417. Madison address: 246 Willowmere Dr., Building D., Madison, MS 39284. website: www.drlarkmere-example.com. o:(601)555-0147 f:(601)555-0183

Target Market(s)

Health care decision makers: primary care doctors and mothers

Contact Information for Business Card

I have no idea; up for any suggestions and I'd do much better picking from examples versus describing what I'm looking for. We are in a very high end location and would like the cards to look really sharp.

Requirements
Must have
• My name, Martin R Belvane, D.C.

```html
<!DOCTYPE html>
<html lang="en">
<head>
<meta charset="utf-8">
<title>Larkmere Chiropractic — Business Card</title>
<link href="https://fonts.googleapis.com/css2?family=Roboto:wght@400&family=Roboto+Condensed:wght@700&display=swap" rel="stylesheet">
<style>
  :root {
    --bg: #d9d4cb;
    --card-white: #fbfbfb;
    --card-black: #0b0b0b;
    --ink: #1a1a1a;
    --ink-soft: #3a3a3a;
    --paper-text: #f4f4f4;
  }
  * { box-sizing: border-box; margin: 0; padding: 0; }
  html, body { width: 1200px; height: 911px; overflow: hidden; }
  body { background: var(--bg); position: relative; font-family: "Roboto", sans-serif; }

  .card {
    position: absolute;
    width: 560px; height: 320px;
    box-shadow: 0 10px 28px rgba(0,0,0,.25);
    overflow: hidden;
  }

  /* Front */
  .card-front { left: 80px; top: 100px; background: var(--card-white); color: var(--ink); }
  .icon-band {
    position: absolute; left: 0; top: 0; bottom: 0; width: 52px;
    background: var(--card-black);
  }
  .icon { position: absolute; left: 16px; width: 20px; height: 20px; }
  .icon svg { width: 20px; height: 20px; fill: var(--paper-text); }

  .doctor-name {
    position: absolute; left: 80px; top: 36px;
    font-family: "Roboto Condensed", sans-serif; font-weight: 700;
    font-size: 22px; letter-spacing: .2px; text-transform: uppercase;
  }
  .contact {
    position: absolute; left: 80px;
    font-size: 15px; line-height: 19px; color: var(--ink-soft);
  }
  .contact-phones { top: 94px; }
  .contact-madison { top: 170px; }
  .contact-campus { top: 232px; }

  .brand {
    position: absolute; right: 36px; top: 34px;
    display: flex; align-items: center; gap: 10px;
    font-family: "Roboto", sans-serif; font-weight: 400;
    color: var(--ink); text-transform: uppercase; line-height: 1.05;
  }
  .brand-mark { width: 12px; height: 12px; border-radius: 50%; background: var(--ink); }
  .brand-name { font-size: 22px; letter-spacing: 1px; }

  /* Back */
  .card-back { left: 560px; top: 480px; background: var(--card-black); color: var(--paper-text); }
  .back-url {
    position: absolute; left: 0; right: 0; top: 46px; text-align: center;
    font-size: 13px; letter-spacing: 7px; text-transform: uppercase;
  }
  .back-brand {
    position: absolute; left: 0; right: 0; top: 140px;
    display: flex; justify-content: center; align-items: center; gap: 14px;
    font-family: "Roboto", sans-serif; font-weight: 400;
    font-size: 34px; letter-spacing: 2px; text-transform: uppercase;
  }
  .back-brand .brand-mark { width: 16px; height: 16px; background: var(--paper-text); }
</style>
</head>
<body>

<section class="card card-front" aria-label="Business card front">
  <div class="icon-band">
    <span class="icon" style="top:38px"><svg viewBox="0 0 24 24"><circle cx="12" cy="7" r="4"/><path d="M4 22c0-5 3.6-8 8-8s8 3 8 8z"/></svg></span>
    <span class="icon" style="top:96px"><svg viewBox="0 0 24 24"><path d="M6.6 10.8a15 15 0 0 0 6.6 6.6l2.2-2.2c.3-.3.7-.4 1-.2 1.1.4 2.3.6 3.6.6.6 0 1 .4 1 1V20c0 .6-.4 1-1 1A17 17 0 0 1 3 4c0-.6.4-1 1-1h3.5c.6 0 1 .4 1 1 0 1.3.2 2.5.6 3.6.1.3 0 .7-.2 1z"/></svg></span>
    <span class="icon" style="top:128px"><svg viewBox="0 0 24 24"><path d="M12 2a10 10 0 1 0 0 20 10 10 0 0 0 0-20zm0 2c1 0 2.3 2.2 2.8 5H9.2C9.7 6.2 11 4 12 4zM4.3 11h3.3a18 18 0 0 0 0 2H4.3a8 8 0 0 1 0-2zm5 0h5.4a16 16 0 0 1 0 2H9.3a16 16 0 0 1 0-2zm7.1 0h3.3a8 8 0 0 1 0 2h-3.3a18 18 0 0 0 0-2zM12 20c-1 0-2.3-2.2-2.8-5h5.6c-.5 2.8-1.8 5-2.8 5z"/></svg></span>
    <span class="icon" style="top:176px"><svg viewBox="0 0 24 24"><path d="M12 2a7 7 0 0 0-7 7c0 5 7 13 7 13s7-8 7-13a7 7 0 0 0-7-7zm0 9.5a2.5 2.5 0 1 1 0-5 2.5 2.5 0 0 1 0 5z"/></svg></span>
    <span class="icon" style="top:238px"><svg viewBox="0 0 24 24"><path d="M12 2a7 7 0 0 0-7 7c0 5 7 13 7 13s7-8 7-13a7 7 0 0 0-7-7zm0 9.5a2.5 2.5 0 1 1 0-5 2.5 2.5 0 0 1 0 5z"/></svg></span>
  </div>

  <h1 class="doctor-name">Martin R Belvane, D.C.</h1>

  <p class="contact contact-phones">(601)555-0147<br>(601)555-0183<br>www.drlarkmere-example.com</p>
  <p class="contact contact-madison">Madison address:<br>246 Willowmere Dr., Building D.<br>Madison, MS 39284.</p>
  <p class="contact contact-campus">Brightvale OrthoCore campus :<br>3815 Pellham Dr., Suite 240<br>Flowood, MS 39417.</p>

  <div class="brand">
    <span class="brand-mark"></span>
    <span class="brand-name">Larkmere<br>Chiropractic</span>
  </div>
</section>

<section class="card card-back" aria-label="Business card back">
  <p class="back-url">www.drlarkmere-example.com</p>
  <div class="back-brand">
    <span class="brand-mark"></span>
    <span>Larkmere Chiropractic</span>
  </div>
</section>

</body>
</html>
```